diamondscoutline.net - Social Media Branding

diamondscoutline.net --> Social Media Re-Branding & Graphics
Facebook: @dmndscoutline - Instagram: @diamondscoutline - Twitter: @dmndscoutline

Looking to find a good designer to help with my diamondscoutline.net social media sites!
- facebook banner
- twitter banner
- instagram template (square and banner size)
- Quote or Information Template
- Committed Template (uniformed) - see the ones I made (& i am no professional) at diamondscoutline.net/committed - needs to have diamondscoutline.net logo, room for: the committed school and the team the player plays on.

Also willing to pay extra for a graphic that is the "complete package" that detail all of the steps of the recruiting process detailed in diamondscoutline.net

Font styles to use
Sans Serif

Colors
ec1f27
fbee3e

```html
<!DOCTYPE html>
<html lang="en">
<head>
<meta charset="utf-8">
<title>Our Complete Package – diamondscoutline.net</title>
<link href="https://fonts.googleapis.com/css2?family=League+Spartan:wght@700;800&family=Jost:wght@400;500&display=swap" rel="stylesheet">
<style>
  :root {
    --brand-red: #be1e2d;
    --ink: #262626;
    --white: #ffffff;
    --sun-yellow: #f5ec5c;
    --sun-orange: #c8312e;
    --sky: #cfe3ef;
    --foliage: #5f7a3e;
  }
  html, body {
    margin: 0;
    padding: 0;
    width: 1099px;
    height: 1200px;
    overflow: hidden;
    background: var(--white);
  }
  .canvas {
    position: relative;
    width: 1099px;
    height: 1200px;
    overflow: hidden;
    background: var(--white);
  }
  .sheet {
    position: absolute;
    left: 12px;
    top: 0;
    width: 1552px;
    height: 1735px;
    transform: scale(0.6917);
    transform-origin: 0 0;
    font-family: "Jost", sans-serif;
    color: var(--ink);
  }
  .title {
    position: absolute;
    left: 252px;
    top: 138px;
    margin: 0;
    font-family: "League Spartan", sans-serif;
    font-weight: 800;
    font-size: 86px;
    line-height: 1;
    letter-spacing: 1px;
    color: var(--ink);
    white-space: nowrap;
  }
  .title .accent { color: var(--brand-red); }
  .roadmap {
    position: absolute;
    left: 0;
    top: 0;
  }
  .step-number {
    font-family: "League Spartan", sans-serif;
    font-weight: 800;
    font-size: 78px;
    fill: var(--white);
  }
  .step {
    position: absolute;
    width: 500px;
  }
  .step h2 {
    margin: 0 0 8px;
    font-family: "League Spartan", sans-serif;
    font-weight: 800;
    font-size: 37px;
    line-height: 37px;
    letter-spacing: 0.5px;
    color: var(--brand-red);
    text-transform: uppercase;
  }
  .step p {
    margin: 0;
    font-size: 26px;
    line-height: 32px;
    color: var(--ink);
  }
  .step--starter   { left: 952px; top: 400px; }
  .step--monthly   { left: 102px; top: 502px; width: 450px; }
  .step--september { left: 952px; top: 652px; width: 500px; }
  .step--offers    { left: 100px; top: 814px; width: 440px; }
  .step--commit    { left: 958px; top: 966px; }
  .step--committed { left: 102px; top: 1120px; }
  .field-photo {
    position: absolute;
    left: 0;
    top: 1290px;
    width: 1552px;
    height: 445px;
    background:
      linear-gradient(180deg, var(--white) 0%, rgba(255,255,255,0) 22%),
      linear-gradient(180deg, var(--sky) 0%, #a9c9db 35%, #7f9a66 62%, var(--foliage) 100%);
  }
  .brand-mark {
    position: absolute;
    left: 420px;
    top: 1505px;
    display: flex;
    align-items: center;
    gap: 28px;
  }
  .brand-mark .dot {
    width: 70px;
    height: 70px;
    border-radius: 50%;
    background: var(--white);
  }
  .brand-mark .name {
    font-family: "Jost", sans-serif;
    font-weight: 500;
    font-size: 54px;
    color: var(--white);
  }
</style>
</head>
<body>
<div class="canvas">
  <div class="sheet">
    <h1 class="title"><span class="accent">OUR</span> COMPLETE PACKAGE</h1>

    <svg class="roadmap" width="1552" height="1735" viewBox="135 132 1552 1735" aria-hidden="true">
      <defs>
        <linearGradient id="step-fill" x1="0" y1="0" x2="1" y2="0">
          <stop offset="0" stop-color="var(--sun-orange)"/>
          <stop offset="1" stop-color="var(--sun-yellow)"/>
        </linearGradient>
      </defs>
      <path d="M466,490 H949 A99 99 0 0 1 949,688 C890,688 870,630 812,630 A97 97 0 0 0 812,824 C870,824 890,768 949,768 A99 99 0 0 1 949,966 C890,966 870,908 812,908 A98 98 0 0 0 812,1104 C870,1104 890,1049 944,1049 A98 98 0 0 1 944,1245 C885,1245 870,1195 812,1195 A97 97 0 0 0 812,1389 H1296"
            fill="none" stroke="var(--brand-red)" stroke-width="32"/>
      <g>
        <circle cx="949" cy="589" r="63" fill="url(#step-fill)"/>
        <text class="step-number" x="949" y="617" text-anchor="middle">1</text>
        <circle cx="812" cy="727" r="63" fill="url(#step-fill)"/>
        <text class="step-number" x="812" y="755" text-anchor="middle">2</text>
        <circle cx="949" cy="866" r="63" fill="url(#step-fill)"/>
        <text class="step-number" x="949" y="894" text-anchor="middle">3</text>
        <circle cx="812" cy="1006" r="63" fill="url(#step-fill)"/>
        <text class="step-number" x="812" y="1034" text-anchor="middle">4</text>
        <circle cx="944" cy="1147" r="63" fill="url(#step-fill)"/>
        <text class="step-number" x="944" y="1175" text-anchor="middle">5</text>
        <circle cx="812" cy="1292" r="63" fill="url(#step-fill)"/>
        <text class="step-number" x="812" y="1320" text-anchor="middle">6</text>
      </g>
    </svg>

    <section class="step step--starter">
      <h2>Starter Pack:</h2>
      <p>Step-by-Step on how to start the<br>Recruiting Process</p>
    </section>
    <section class="step step--monthly">
      <h2>Monthly Lesson:</h2>
      <p>Breakdown of what you should be doing (email, video, social media &amp; MORE) every month to build relationships with college coaches</p>
    </section>
    <section class="step step--september">
      <h2>Preparing for September 1st (Junior Year)</h2>
      <p>How to Prepare for Calls &amp; What to<br>Say to College Coaches</p>
    </section>
    <section class="step step--offers">
      <h2>Turning Phone Calls into Offers</h2>
      <p>Talking with Schools? - How to get<br>the Offer</p>
    </section>
    <section class="step step--commit">
      <h2>How to Commit:</h2>
      <p>What Questions to Ask &amp; What to<br>get in Writing</p>
    </section>
    <section class="step step--committed">
      <h2>Committed:</h2>
      <p>Learn Everything you Need to Do<br>After you Say "YES!"</p>
    </section>

    <div class="field-photo" role="img" aria-label="Photo of a softball batter in a helmet at the plate with a catcher, trees and sky behind"></div>
    <div class="brand-mark">
      <span class="dot"></span>
      <span class="name">diamondscoutline.net</span>
    </div>
  </div>
</div>
</body>
</html>
```